Managed IT services business card design

We haven't needed a business card since the founding of the business in 2005. All our clients have been coming through word of mouth. And lately more and more existing clients are requesting for our business cards to pass on to their contacts in recommending us.
So we needing a business card design. We use various innovative solutions and methodologies to provide IT services to small businesses in managing their IT systems. Our role is the same as an in-house, full-time IT Manager for our clients, but outsourced. So we take care of all our clients' IT needs, just as an IT Manager would be expected to perform.
We have a holding website, which we're happy to leave for now. If we can use the same logo would be great - www.lumadesk.com.au
Preferred colours are shades of are white, grey and black.
We pride our business with the following traits: proactive, good service, prompt response, trustworthy.
Target Market(s)
Small businesses of any industry
Industry/Entity Type
Business

```html
<!DOCTYPE html>
<html lang="en">
<head>
<meta charset="utf-8">
<title>Lumadesk business card</title>
<link rel="stylesheet" href="https://fonts.googleapis.com/css2?family=Open+Sans:wght@400&display=swap">
<style>
  :root {
    --backdrop: #e4e5e6;
    --card-grey: #5a5f62;
    --card-white: #ffffff;
    --ink: #1c1a1a;
    --swoosh: #231f1f;
    --on-grey: #f4f4f4;
    --icon-grey: #6b6e70;
  }
  * { box-sizing: border-box; margin: 0; padding: 0; }
  html, body {
    width: 1200px; height: 680px; overflow: hidden;
    background: var(--backdrop);
    font-family: "Open Sans", Arial, sans-serif;
  }
  .stage {
    width: 1200px; height: 680px;
    display: flex; align-items: center; justify-content: center; gap: 60px;
  }
  .card {
    position: relative; width: 540px; height: 310px;
    border-radius: 18px; overflow: hidden;
    box-shadow: 0 6px 18px rgba(0,0,0,0.18);
  }
  .card-shape { position: absolute; inset: 0; }
  .holder { position: absolute; top: 28px; right: 34px; text-align: right; color: var(--on-grey); }
  .holder-name { font-size: 18px; }
  .holder-role { font-size: 12px; margin-top: -2px; }
  .brand {
    position: absolute; display: flex; align-items: center; gap: 12px;
    font-weight: 400; color: var(--ink);
  }
  .brand-dot { flex: none; border-radius: 50%; background: currentColor; }
  .front .brand { left: 48px; top: 178px; font-size: 30px; }
  .front .brand-dot { width: 12px; height: 12px; }
  .address {
    position: absolute; right: 36px; top: 128px; text-align: right;
    font-size: 15px; line-height: 1.25; color: var(--ink);
  }
  .contacts {
    position: absolute; left: 44px; top: 226px; list-style: none;
    font-size: 14px; line-height: 1.2; color: var(--ink);
  }
  .contacts li { display: flex; align-items: center; gap: 10px; height: 17px; }
  .contacts svg { width: 13px; height: 13px; flex: none; }
  .back { background: var(--card-grey); }
  .back .brand {
    left: 0; right: 0; top: 112px; justify-content: center;
    font-size: 46px; color: var(--on-grey); gap: 16px;
  }
  .back .brand-dot { width: 16px; height: 16px; }
  .back-web {
    position: absolute; right: 40px; bottom: 40px;
    font-size: 12px; letter-spacing: 0.35em; color: var(--on-grey);
  }
</style>
</head>
<body>
<main class="stage">
  <section class="card front" aria-label="Card front">
    <svg class="card-shape" viewBox="0 0 540 310" aria-hidden="true">
      <rect width="540" height="310" fill="var(--card-grey)"/>
      <path d="M0,168 Q260,48 540,84 L540,310 L0,310 Z" fill="var(--card-white)"/>
      <path d="M0,146 Q250,34 540,80 Q262,52 0,172 Z" fill="var(--swoosh)"/>
    </svg>
    <div class="holder">
      <p class="holder-name">Mara Quillet</p>
      <p class="holder-role">director</p>
    </div>
    <p class="brand"><span>Lumadesk</span><span class="brand-dot"></span></p>
    <p class="address">1480 Elm Row Rd<br>Carver TX 78010</p>
    <ul class="contacts">
      <li>
        <svg viewBox="0 0 14 14" aria-label="Phone" role="img"><path d="M3 1 L5 1 L6 4 L4.5 5 Q5.5 8 9 9.5 L10 8 L13 9 L13 11 Q12 13 10 13 Q2 11 1 3 Q1 1 3 1 Z" fill="var(--icon-grey)"/></svg>
        512 014 2290
      </li>
      <li>
        <svg viewBox="0 0 14 14" aria-label="Fax" role="img"><rect x="4" y="1" width="6" height="5" fill="none" stroke="var(--icon-grey)"/><rect x="1" y="6" width="12" height="6" rx="1" fill="var(--icon-grey)"/></svg>
        512 014 2291
      </li>
      <li>
        <svg viewBox="0 0 14 14" aria-label="Email" role="img"><rect x="1" y="3" width="12" height="8" fill="var(--icon-grey)"/><path d="M1 3 L7 8 L13 3" fill="none" stroke="#fff"/></svg>
        info@lumadesk.com.au
      </li>
      <li>
        <svg viewBox="0 0 14 14" aria-label="Website" role="img"><circle cx="7" cy="7" r="6" fill="var(--icon-grey)"/><path d="M1 7 H13 M7 1 V13 M3 3.5 H11 M3 10.5 H11" stroke="#fff" stroke-width="0.7"/></svg>
        www.lumadesk.com.au
      </li>
    </ul>
  </section>

  <section class="card back" aria-label="Card back">
    <p class="brand"><span>Lumadesk</span><span class="brand-dot"></span></p>
    <p class="back-web">www.lumadesk.com.au</p>
  </section>
</main>
</body>
</html>
```